Business Card Design For A Renovation Contractor Company

We need a business card for a new company based in Singapore, our company name is "RB Tolvane". We are a renovation contractor that builds designs into reality. We build more of F&B restaurants, retail stores and commercial offices. We work very closely with designers. The final design should communicate to our client that we are a company that you can trust, that will plan and complete your project without giving you a headache. I like my client to remember my company as "RB". The beauty of SIMPLE is important.

Industry/Entity Type

Contractor

Requirements
Nice to have
• Black or Red base

```html
<!DOCTYPE html>
<html lang="en">
<head>
<meta charset="utf-8">
<title>RB Tolvane — Business Card</title>
<link rel="stylesheet" href="https://fonts.googleapis.com/css2?family=Lato:wght@300;400;700&display=swap">
<style>
  :root {
    --page: #d9d6d2;
    --card-light: #e9e9e9;
    --card-dark: #222222;
    --ink: #2a2a2a;
    --red: #c4161c;
    --white: #f4f4f4;
  }
  * { margin: 0; padding: 0; box-sizing: border-box; }
  html, body {
    width: 1200px; height: 900px; overflow: hidden;
    background: var(--page);
    font-family: 'Lato', sans-serif;
  }
  .canvas { position: relative; width: 1200px; height: 900px; }
  .card {
    position: absolute; left: 320px; width: 560px; height: 320px;
    box-shadow: 0 6px 18px rgba(0,0,0,.18);
    overflow: hidden;
  }
  /* Back side */
  .card-back { top: 100px; background: var(--card-dark); }
  .back-mark {
    position: absolute; inset: 0;
    display: flex; align-items: center; justify-content: center; gap: 18px;
  }
  .back-dot { width: 26px; height: 26px; border-radius: 50%; background: var(--red); }
  .back-name { color: var(--red); font-weight: 300; font-size: 46px; letter-spacing: 1px; }
  /* Front side */
  .card-front { top: 480px; background: var(--card-light); color: var(--ink); }
  .brand { position: absolute; left: 40px; top: 70px; }
  .brand-row { display: flex; align-items: center; gap: 12px; }
  .brand-dot { width: 20px; height: 20px; border-radius: 50%; background: var(--red); }
  .brand-name { font-weight: 400; font-size: 34px; color: var(--ink); line-height: 1; }
  .brand-tagline {
    margin-top: 6px; padding-top: 4px;
    border-top: 1px solid var(--ink);
    font-size: 12px; font-weight: 400; color: var(--ink); letter-spacing: .3px;
  }
  .person { position: absolute; left: 40px; top: 170px; }
  .person-name { font-size: 20px; font-weight: 400; letter-spacing: .5px; }
  .person-role { font-size: 15px; font-weight: 400; margin-top: 2px; }
  .contact { position: absolute; right: 36px; top: 62px; font-size: 13px; line-height: 20px; }
  .contact-row { display: flex; gap: 10px; }
  .contact-label { color: var(--red); font-weight: 700; width: 10px; }
  .contact-web { margin-left: 20px; font-weight: 700; }
  .contact-web .accent { color: var(--red); }
  .address-band {
    position: absolute; left: 0; right: 0; bottom: 0; height: 54px;
    background: var(--card-dark); color: var(--white);
    display: flex; align-items: center; justify-content: center;
    font-size: 15px; letter-spacing: .3px;
  }
</style>
</head>
<body>
<main class="canvas">
  <section class="card card-back" aria-label="Card back">
    <div class="back-mark">
      <span class="back-dot"></span>
      <span class="back-name">RB Tolvane</span>
    </div>
  </section>

  <section class="card card-front" aria-label="Card front">
    <div class="brand">
      <div class="brand-row">
        <span class="brand-dot"></span>
        <span class="brand-name">RB Tolvane</span>
      </div>
      <p class="brand-tagline">fit-outs finished as planned</p>
    </div>

    <div class="person">
      <p class="person-name">MARCUS LIM.</p>
      <p class="person-role">Director</p>
    </div>

    <div class="contact">
      <p class="contact-row"><span class="contact-label">T</span><span>655.204.3187</span></p>
      <p class="contact-row"><span class="contact-label">E</span><span>marcus@rbtolvane.com</span></p>
      <p class="contact-web">www.<span class="accent">rbtolvane</span>.com</p>
    </div>

    <div class="address-band">12 Serin Road, #04-108 Serin Court, Singapore 428110</div>
  </section>
</main>
</body>
</html>
```